Construction Company

Design a clutter free business card, it can be double-sided utilizing the logo for VKM Ltd simple with all relevant contact information.

Please also a letterhead design to function for the purposes of invoicing, all mail requirements, with header to be distinctive while the footer ties page together and incorporates all necessary information.

For now, please use generic / dummy text and when a winner is selected, I will disclose the contact information.

Hi Designers! Please read the updated brief which includes the design of a business card and letterhead. Thank you!

```html
<!DOCTYPE html>
<html lang="en">
<head>
<meta charset="UTF-8">
<title>VKM Ltd — Business Card</title>
<link rel="stylesheet" href="https://fonts.googleapis.com/css2?family=Work+Sans:wght@400;500;600&display=swap">
<style>
  :root {
    --backdrop: #141414;
    --card: #222222;
    --card-edge: #1a1a1a;
    --gold: #c9a227;
    --royal-blue: #1838a8;
    --silver: #9a9a9a;
    --ink-light: #f2f2f2;
  }
  * { margin: 0; padding: 0; box-sizing: border-box; }
  html, body {
    width: 1200px;
    height: 900px;
    overflow: hidden;
    background: var(--backdrop);
    font-family: "Work Sans", Arial, sans-serif;
  }
  .canvas {
    width: 1200px;
    height: 900px;
    display: flex;
    flex-direction: column;
    align-items: center;
    justify-content: center;
    gap: 50px;
  }
  .card {
    position: relative;
    width: 630px;
    height: 360px;
    background: linear-gradient(135deg, var(--card) 0%, var(--card-edge) 100%);
    border-bottom: 5px solid var(--gold);
    overflow: hidden;
  }
  .card-front {
    display: flex;
    align-items: center;
    justify-content: center;
  }
  .wordmark {
    display: flex;
    align-items: center;
    gap: 14px;
    font-weight: 600;
    letter-spacing: 0.04em;
  }
  .wordmark-dot {
    width: 18px;
    height: 18px;
    border-radius: 50%;
  }
  .card-front .wordmark { color: var(--silver); font-size: 64px; }
  .card-front .wordmark-dot { background: var(--silver); width: 22px; height: 22px; }

  .card-back {
    display: flex;
    align-items: center;
    padding: 0 40px 0 44px;
  }
  .card-back .wordmark { color: var(--royal-blue); font-size: 48px; width: 270px; }
  .card-back .wordmark-dot { background: var(--royal-blue); }
  .divider {
    width: 2px;
    height: 190px;
    background: var(--gold);
    margin: 0 30px 0 10px;
  }
  .contact { color: var(--ink-light); font-size: 17px; line-height: 1.4; }
  .contact-name {
    color: var(--gold);
    font-size: 23px;
    font-weight: 600;
    letter-spacing: 0.05em;
    text-transform: uppercase;
  }
  .contact-role { margin-bottom: 14px; }
  .contact-address { margin-bottom: 8px; }
  .contact-line {
    display: flex;
    align-items: center;
    gap: 10px;
  }
  .contact-line svg { width: 14px; height: 14px; flex: none; }
</style>
</head>
<body>
<main class="canvas">
  <section class="card card-front" aria-label="Business card front">
    <div class="wordmark"><span class="wordmark-dot"></span>VKM LTD</div>
  </section>

  <section class="card card-back" aria-label="Business card back">
    <div class="wordmark"><span class="wordmark-dot"></span>VKM LTD</div>
    <div class="divider"></div>
    <div class="contact">
      <p class="contact-name">Daniel Reeves</p>
      <p class="contact-role">Founder</p>
      <p class="contact-address">2750 Harbor Lane<br>Springfield, DE 19800</p>
      <p class="contact-line">
        <svg viewBox="0 0 24 24" fill="none" stroke="var(--gold)" stroke-width="2"><path d="M5 3h4l2 5-3 2a12 12 0 0 0 6 6l2-3 5 2v4a2 2 0 0 1-2 2A17 17 0 0 1 3 5a2 2 0 0 1 2-2z"/></svg>
        (555) 214-7390
      </p>
      <p class="contact-line">
        <svg viewBox="0 0 24 24" fill="none" stroke="var(--gold)" stroke-width="2"><rect x="3" y="5" width="18" height="14" rx="1"/><path d="M3 6l9 7 9-7"/></svg>
        info@vkmltd.com
      </p>
      <p class="contact-line">
        <svg viewBox="0 0 24 24" fill="none" stroke="var(--gold)" stroke-width="2"><circle cx="12" cy="12" r="9"/><path d="M3 12h18M12 3c3 3 3 15 0 18M12 3c-3 3-3 15 0 18"/></svg>
        www.vkmltd.com
      </p>
    </div>
  </section>
</main>
</body>
</html>
```